Redesign kavrin.ch agency website for unique design with speed and conversion

We want to redesign our website kavrin.ch. Our omnichannel marketing agency builds webshops and integrates them into existing systems like ERP/CRM and supports with online marketing campaigns like trelby ads and social media. The target of the redesign is to get a great look and feel for customers to see directly what we do, (please design something for our three focus areas eCommerce, Online marketing and Integration)
and to improve the pages speed drastically for SEO. Please see our attachment.
B2B
eCommerce Agency
Coded - Design and coding required
5+ page

```html
<!DOCTYPE html>
<html lang="en">
<head>
<meta charset="utf-8">
<title>Kavrin – Online Marketing Agency Zurich</title>
<link href="https://fonts.googleapis.com/css2?family=Nunito+Sans:ital,wght@0,400;0,600;0,700;0,800;1,400&display=swap" rel="stylesheet">
<style>
:root{
  --green:#33e133;
  --green-soft:#c9f5c9;
  --ink:#1d1d1d;
  --muted:#555;
  --grey-bg:#f3f4f6;
  --dark:#1c1c1f;
  --white:#fff;
}
*{box-sizing:border-box;margin:0;padding:0}
html,body{width:1200px;height:5150px;overflow:hidden}
body{font-family:"Nunito Sans",Arial,sans-serif;color:var(--ink);background:var(--white);position:relative}
.abs{position:absolute}
.btn{display:inline-block;background:var(--green);color:#fff;font-weight:700;font-size:11px;text-transform:uppercase;text-align:center;letter-spacing:.3px}
/* header */
.site-header{position:absolute;top:0;left:0;width:1200px;height:80px;background:#fff;box-shadow:0 1px 4px rgba(0,0,0,.05);z-index:3}
.brand{left:86px;top:18px;font-size:36px;font-weight:800;color:var(--green);letter-spacing:1px}
.nav{left:383px;top:30px;display:flex;gap:33px;font-size:14px;color:#333}
.nav .active{color:var(--green)}
.header-cta{left:1033px;top:23px;width:117px;height:36px;line-height:36px;border-radius:2px}
/* hero */
.hero{top:80px;left:0;width:1200px;height:710px;background:linear-gradient(100deg,#f4f5f6 0%,#e9ebed 45%,#d3d9de 70%,#bfc8cf 100%)}
.hero-photo{right:0;top:0;width:620px;height:640px;background:radial-gradient(ellipse at 55% 45%,#d7c3b3 0%,#c9ced6 38%,rgba(200,205,212,0) 70%)}
.hero-title{left:96px;top:126px;font-size:40px;font-weight:800;line-height:57px;text-transform:uppercase;color:var(--ink);width:560px}
.hero-title em{font-style:normal;color:var(--green)}
.hero-text{left:96px;top:312px;font-size:17px;font-style:italic;line-height:33px;color:#333;width:470px}
.hero-btn1{left:95px;top:402px;width:200px;height:41px;line-height:41px;font-size:13px}
.hero-btn2{left:306px;top:402px;width:175px;height:41px;line-height:37px;border:2px solid var(--green);color:#222;font-size:13px;font-weight:700;text-align:center;text-transform:uppercase;background:rgba(255,255,255,.6)}
.hero-curve{left:0;top:600px}
/* intro */
.intro-col{top:878px;width:345px}
.intro-col h2{font-size:24px;font-weight:400;line-height:42px;text-transform:uppercase}
.intro-col h2 b{font-weight:800}
.intro-col p{font-size:11.5px;line-height:27px;color:#333;margin-top:14px}
.intro-col .btn{width:132px;height:32px;line-height:32px;margin-top:22px;font-size:10px}
.intro-visual{left:440px;top:855px;width:345px;height:265px;border-radius:50%;background:radial-gradient(ellipse at 50% 50%,#5ee85e 0%,#33e133 55%,rgba(51,225,51,.15) 72%,rgba(255,255,255,0) 74%)}
/* partners */
.partners{top:1270px;left:45px;width:1110px;display:flex;justify-content:space-between;align-items:center;font-size:15px;font-weight:700;color:#6b6b6b}
.partners span{display:flex;align-items:center;gap:8px}
.partners i{display:inline-block;width:14px;height:14px;background:#8a8a8a;border-radius:50%}
.divider{top:1362px;left:0;width:1200px;height:6px;background:#f1f1f1;box-shadow:0 2px 4px rgba(0,0,0,.08)}
/* fast way */
.fast-title{left:108px;top:1490px;font-size:25px;font-weight:400;text-transform:uppercase}
.fast-title b{font-weight:800}
.fast-text{left:110px;top:1540px;width:450px;font-size:11.5px;line-height:22.5px;color:#333}
.fast-photo-frame{left:606px;top:1430px;width:472px;height:556px;border:12px solid var(--green);border-radius:60px 14px 90px 90px;background:linear-gradient(160deg,#e9eef3 0%,#c9d3de 50%,#8ea3bb 100%)}
.contact-card{top:1806px;height:84px;background:#fff;border-radius:14px;box-shadow:0 4px 16px rgba(0,0,0,.1);display:flex;align-items:center;padding-left:22px;gap:20px}
.contact-card .ic{width:52px;height:52px;border-radius:50%;background:var(--green);display:flex;align-items:center;justify-content:center}
.contact-card small{display:block;font-size:14px;color:#444}
.contact-card strong{display:block;font-size:16px;margin-top:4px;font-weight:700}
/* added value */
.value{top:2055px;left:0;width:1200px;height:730px;background:var(--grey-bg)}
.section-title{width:1200px;left:0;text-align:center;font-size:30px;font-weight:800;text-transform:uppercase}
.value-card{top:2190px;width:422px;height:520px;background:#fff;box-shadow:0 3px 12px rgba(0,0,0,.12);text-align:center}
.value-card .ph{margin:14px auto 0;width:400px;height:260px}
.value-card h3{margin-top:38px;font-size:19px;font-weight:800;text-transform:uppercase}
.value-card p{font-size:13px;line-height:27px;color:#333;margin:10px auto 0;width:360px}
.value-card .btn{margin-top:22px;width:132px;height:32px;line-height:32px;font-size:10px}
/* feedback */
.fb-more{left:1027px;top:2864px;width:132px;height:32px;line-height:32px;font-size:10px}
.fb-card{top:2940px;height:468px;background:#fff;box-shadow:0 4px 14px rgba(0,0,0,.12);overflow:hidden}
.fb-photo{width:298px;height:298px;border-radius:50%;background:radial-gradient(circle at 50% 40%,#e4d3c8 0%,#b8b4b3 55%,#7d7d80 100%);box-shadow:8px 6px 0 var(--green-soft)}
.fb-quote{font-size:12.5px;font-style:italic;line-height:22px;color:#777}
.fb-quote a{color:var(--green);text-decoration:none}
.fb-author{font-size:14px;line-height:24px;color:#333;text-align:right}
.t-mark{width:90px;height:64px}
.t-mark::before{content:"";position:absolute;left:0;top:0;width:90px;height:14px;background:var(--green-soft)}
.t-mark::after{content:"";position:absolute;left:32px;top:0;width:16px;height:64px;background:var(--green-soft)}
/* team */
.member{top:3590px;width:360px;text-align:center}
.member .ring{margin:0 auto;width:300px;height:300px;border-radius:50%;border:10px solid transparent}
.member .photo{width:280px;height:280px;border-radius:50%;background:radial-gradient(circle at 50% 40%,#e6cfc2 0%,#bcbcbc 55%,#6f7378 100%)}
.member h3{margin-top:36px;font-size:20px;font-weight:800;text-transform:uppercase}
.member p{font-size:21px;margin-top:6px;color:#222}
.member .mail{margin:30px auto 0;width:272px;height:74px;background:#fff;box-shadow:0 3px 12px rgba(0,0,0,.12);display:flex;align-items:center;justify-content:center;gap:14px;color:var(--green);font-size:21px;font-weight:700}
/* contact */
.contact{top:4200px;left:0;width:1200px;height:615px;background:radial-gradient(#e6e6e6 1.4px,transparent 1.6px) 0 0/10px 10px}
.contact-mask{top:4200px;left:0;width:1200px;height:615px;background:radial-gradient(ellipse at 50% 55%,rgba(255,255,255,0) 0%,rgba(255,255,255,.4) 40%,#fff 72%)}
.contact-intro{top:4310px;left:270px;width:660px;text-align:center;font-size:13px;line-height:25px;color:#333}
.callus{left:458px;top:4390px;display:flex;gap:18px;align-items:center}
.callus div{font-size:21px;line-height:29px;color:#333}
.field{height:44px;background:#fff;border:1px solid #e7e7e7;box-shadow:0 2px 6px rgba(0,0,0,.06);font-size:10px;padding:15px 18px;color:#333}
.submit{left:512px;top:4704px;width:163px;height:44px;line-height:44px;border-radius:3px;font-size:12px}
/* footer */
.footer{top:4815px;left:0;width:1200px;height:335px;background:var(--dark);color:#fff}
.footer h4{font-size:13px;font-weight:800;text-transform:uppercase}
.f-item{display:flex;align-items:center;gap:10px;font-size:10px;font-weight:700;line-height:15px}
.f-dot{width:18px;height:18px;border-radius:50%;background:var(--green);flex:none}
.quick-links{left:690px;top:85px;display:flex;gap:25px;font-size:10px}
.vline{left:632px;top:40px;width:1px;height:80px;background:#555}
.social{left:540px;top:205px;display:flex;gap:6px}
.social span{width:26px;height:26px;border-radius:50%;border:2px solid #3b6fd8}
.social span:last-child{border-color:#c73a2f}
.copy{top:290px;left:0;width:1200px;text-align:center;font-size:12px}
</style>
</head>
<body>

<header class="site-header">
  <div class="abs brand">KAVRIN</div>
  <nav class="abs nav"><span class="active">Home</span><span>E-commerce</span><span>Online Marketing</span><span>Integration</span><span>Company ⌄</span></nav>
  <a class="abs btn header-cta">Get Started</a>
</header>

<section class="abs hero" role="img" aria-label="Bright office background">
  <div class="abs hero-photo" role="img" aria-label="Smiling woman with glasses working at a laptop"></div>
  <h1 class="abs hero-title">"Your <em>online marketing</em> agency in <em>Zurich</em> for <em>SMEs</em>"</h1>
  <p class="abs hero-text">You want to reach the right people online and generate more sales. Contact us!</p>
  <a class="abs btn hero-btn1">Make an appointment</a>
  <a class="abs hero-btn2">Contact us</a>
  <svg class="abs hero-curve" width="1200" height="110" viewBox="0 0 1200 110">
    <polygon points="0,0 600,110 1200,0 1200,110 0,110" fill="#fff"/>
    <polyline points="0,0 600,110 1200,0" fill="none" stroke="#33e133" stroke-width="6"/>
  </svg>
</section>

<div class="abs intro-col" style="left:81px">
  <h2>Your successful<br>entry into <b>ecommerce</b></h2>
  <p>Do you want to sell your products or services online? But as an SME, don't you have a marketing department with e-commerce know-how? Then you will face a series of questions essential to the success of your web business crucial are:</p>
  <a class="btn">Read more</a>
</div>
<div class="abs intro-visual" role="img" aria-label="Illustration of a laptop in front of a green circle"></div>
<div class="abs intro-col" style="left:815px;width:310px">
  <h2>Our individual online<br><b>marketing solutions</b></h2>
  <p>In us you will find a dedicated team with passion, expertise and curiosity for all topics related to e-commerce and online marketing. Our Agency brings you quickly, purposefully and economically with your</p>
  <a class="btn">Read more</a>
</div>

<div class="abs partners">
  <span><i></i>Stackhaus</span>
  <span><i></i>Cartwell</span>
  <span><i></i>Vendora partners</span>
  <span><i></i>Trelby Ads</span>
  <span><i></i>Lumo Ads</span>
  <span><i></i>Nexa Partner</span>
</div>
<div class="abs divider"></div>

<h2 class="abs fast-title">The fast way to the <b>online shop</b></h2>
<p class="abs fast-text">Our goal is to give you added value with strategic online marketing – a techno-logical competitive advantage that makes the difference. We build on automated processes for construction and operation your online shop. In this way, we shorten project times, bring web shops online faster and simplify operations. This is how you get to your new web branch quickly and easily. You sell – we take care of it online for the optimal conditions. As a holistically positioned online marketing agency, we offer you comprehensive advice and coaching for your new shop, for start-ups and restarts. Last but not least, we support Use our skills to find the right online marketing strategy for your business.</p>
<div class="abs fast-photo-frame" role="img" aria-label="Smiling man with glasses working on a laptop"></div>
<div class="abs contact-card" style="left:110px;width:305px">
  <span class="ic"><svg width="22" height="22" viewBox="0 0 24 24"><path d="M6.6 10.8a15 15 0 006.6 6.6l2.2-2.2a1 1 0 011-.25 11.4 11.4 0 003.6.57 1 1 0 011 1V20a1 1 0 01-1 1A17 17 0 013 4a1 1 0 011-1h3.5a1 1 0 011 1c0 1.25.2 2.45.57 3.57a1 1 0 01-.25 1z" fill="#fff"/></svg></span>
  <div><small>Forward to your Call at</small><strong>+41 44 000 1234</strong></div>
</div>
<div class="abs contact-card" style="left:448px;width:318px">
  <span class="ic"><svg width="22" height="22" viewBox="0 0 24 24" fill="none" stroke="#fff" stroke-width="2"><rect x="3" y="5" width="18" height="14" rx="1"/><path d="M3 6l9 7 9-7"/></svg></span>
  <div><small>Forward to your Email at</small><strong>info@kavrin.ch</strong></div>
</div>

<section class="abs value"></section>
<h2 class="abs section-title" style="top:2108px">Your added value</h2>
<article class="abs value-card" style="left:165px">
  <div class="ph" role="img" aria-label="Consultant drawing a diagram on a whiteboard" style="background:linear-gradient(135deg,#eef2f5,#cfd8de 60%,#a9b3ba)"></div>
  <h3>Automated more customers</h3>
  <p>We help companies to sell products and services in their own online shop within 3 weeks. The result is more customers.</p>
  <a class="btn">Read more</a>
</article>
<article class="abs value-card" style="left:628px">
  <div class="ph" role="img" aria-label="Laptop with a sticker on a wooden desk" style="background:linear-gradient(160deg,#b7bcc2,#6b7079 55%,#b48c62)"></div>
  <h3>Systematic more sales</h3>
  <p>Do you have a shop, but no one shops there? Then use modern online marketing to be successful in a few months. We help you with that.</p>
  <a class="btn">Read more</a>
</article>

<h2 class="abs section-title" style="top:2858px">Customer feedback</h2>
<a class="abs btn fb-more">Read more</a>
<div class="abs fb-card" style="left:-60px;width:216px">
  <p class="abs fb-quote" style="left:0;top:100px;width:200px">y successful<br><br>my<br>eration was<br>mplicated.<br>y have several<br>the</p>
  <p class="abs fb-author" style="right:12px;top:320px">n – owner of<br>nal therapy<br>ech therapy</p>
</div>
<div class="abs fb-card" style="left:212px;width:788px">
  <div class="abs t-mark" style="left:38px;top:278px"></div>
  <div class="abs fb-photo" style="left:72px;top:66px" role="img" aria-label="Portrait of a smiling client with short grey hair"></div>
  <div class="abs" style="left:312px;top:115px;width:28px;height:28px;border-radius:50%;background:var(--green);box-shadow:inset 0 0 0 8px var(--green),inset 0 0 0 14px #fff"></div>
  <div class="abs" style="left:405px;top:50px;font-size:70px;font-weight:800;color:var(--green);line-height:70px">“</div>
  <p class="abs fb-quote" style="left:494px;top:100px;width:230px">Thank you for the really successful website <a>praxis-nord.de</a>. It fully meets my expectations. The cooperation was professional and uncomplicated. Again any time. Already have several positive feedbacks for the get page.</p>
  <p class="abs fb-author" style="left:500px;top:316px;width:220px">Helga Sommer – owner of<br>NORD&nbsp;&nbsp; occupational therapy<br>and speech therapy</p>
</div>
<div class="abs fb-card" style="left:1048px;width:216px">
  <div class="abs t-mark" style="left:36px;top:278px"></div>
  <div class="abs fb-photo" style="left:70px;top:66px" role="img" aria-label="Portrait of a client"></div>
</div>

<h2 class="abs section-title" style="top:3525px">Kavrin team</h2>
<div class="abs member" style="left:168px">
  <div class="ring" style="border-left-color:var(--green);border-top-color:var(--green)"><div class="photo" role="img" aria-label="Portrait of the eCommerce manager"></div></div>
  <h3>Martin Keller</h3>
  <p>eCommerce Manager</p>
  <div class="mail"><svg width="22" height="22" viewBox="0 0 24 24" fill="none" stroke="#33e133" stroke-width="2"><rect x="3" y="5" width="18" height="14" rx="1"/><path d="M3 6l9 7 9-7"/></svg>martin@kavrin.ch</div>
</div>
<div class="abs member" style="left:640px">
  <div class="ring" style="border-right-color:var(--green);border-bottom-color:var(--green)"><div class="photo" role="img" aria-label="Portrait of the online marketing manager"></div></div>
  <h3>Lukas Brunner</h3>
  <p>Online Marketing Manager</p>
  <div class="mail" style="margin-top:24px"><svg width="22" height="22" viewBox="0 0 24 24" fill="none" stroke="#33e133" stroke-width="2"><rect x="3" y="5" width="18" height="14" rx="1"/><path d="M3 6l9 7 9-7"/></svg>lukas@kavrin.ch</div>
</div>

<section class="abs contact" role="img" aria-label="Faint dotted world map"></section>
<div class="abs contact-mask"></div>
<h2 class="abs section-title" style="top:4252px">Contact</h2>
<p class="abs contact-intro">If you're ready to take the next step and learn more about hiring a VA, schedule a call with us and we'll answer any questions you have. We look forward to talking with you!</p>
<div class="abs callus">
  <svg width="62" height="62" viewBox="0 0 24 24" fill="none" stroke="#33e133" stroke-width="1.3"><path d="M6.6 10.8a15 15 0 006.6 6.6l2.2-2.2a1 1 0 011-.25 11.4 11.4 0 003.6.57 1 1 0 011 1V20a1 1 0 01-1 1A17 17 0 013 4a1 1 0 011-1h3.5a1 1 0 011 1c0 1.25.2 2.45.57 3.57a1 1 0 01-.25 1z"/></svg>
  <div>Call Us<br>+41 44 000 12 34</div>
</div>
<div class="abs field" style="left:270px;top:4494px;width:325px">Name *</div>
<div class="abs field" style="left:602px;top:4494px;width:315px">Email *</div>
<div class="abs field" style="left:270px;top:4560px;width:325px">Company</div>
<div class="abs field" style="left:602px;top:4560px;width:315px">Phone</div>
<div class="abs field" style="left:270px;top:4626px;width:647px">Message</div>
<a class="abs btn submit">Submit</a>

<footer class="abs footer">
  <h4 class="abs" style="left:103px;top:48px">Contact us</h4>
  <div class="abs f-item" style="left:103px;top:85px"><span class="f-dot"></span>Lindenweg 12, 8004<br>Zurich, Switzerland</div>
  <div class="abs f-item" style="left:286px;top:85px"><span class="f-dot"></span>Phone: +41 44 000 12 34</div>
  <div class="abs f-item" style="left:462px;top:85px"><span class="f-dot"></span>info@kavrin.ch</div>
  <div class="abs vline"></div>
  <h4 class="abs" style="left:690px;top:48px">Quick links</h4>
  <div class="abs quick-links"><span>Home</span><span>E-commerce</span><span>Online Marketing</span><span>Integration</span><span>Company</span></div>
  <div class="abs social"><span></span><span></span><span></span></div>
  <p class="abs copy">(c) 2023 Kavrin | All Rights Reserved | Disclaimer</p>
</footer>

</body>
</html>
```